Website for my photography business

I need a website for my photography business, Bram Kellet Photography. I need a website that has a landing page with a cover photo of each kind of photography I do. For example, Nature, Weddings, Portraits and Architecture. I want it so that when someone comes onto my website they have to choose which kind of photography page they want to visit. So if they click on the wedding photo it will open to a page with my wedding portfolio images and a contact me button. If they choose nature photography I want them to be redirected to an e-commerce section where they can purchase prints. Architecture and Portraits should open up to their respective portfolios with about me and contact info. I like this kind of format because I want people who come to my website for a specific type of photography to be able to be directed there easily without having to look at a mix of other kinds of photography. I will provide a few files to use as placeholders. I have already purchased the bramkelletphotography.example domain name. A Wix website would be great because I am most familiar with it but I am open to anything.

Industry/Entity Type

Photographer

Number of Pages Required

5+ page

Requirements
Must have
• Landing Page and e-commerce

```html
<!DOCTYPE html>
<html lang="en">
<head>
<meta charset="utf-8">
<title>Bram Kellet Photography – Nature</title>
<link rel="stylesheet" href="https://fonts.googleapis.com/css2?family=Poppins:wght@400;500;600&family=Parisienne&display=swap">
<style>
:root{
  --purple:#3e3669;
  --navy:#1f5170;
  --navy-dark:#1d4a66;
  --ink:#333;
  --muted:#555;
  --card:#f7f7f7;
  --line:#e1e1e1;
  --soft:#f4f4f4;
  --white:#fff;
}
*{box-sizing:border-box;margin:0;padding:0}
html,body{width:1200px;height:3107px;overflow:hidden}
body{font-family:"Poppins",sans-serif;color:var(--ink);background:var(--white);position:relative}
.script{font-family:"Parisienne",cursive;font-weight:400}
.abs{position:absolute}

.topbar{top:0;left:0;width:1200px;height:32px;border-bottom:1px solid #e6e6e6;font-size:13px;color:#555;text-align:center;line-height:31px}
.header{top:32px;left:0;width:1200px;height:101px}
.brand{left:112px;top:30px;display:flex;align-items:center;gap:12px;font-size:22px;color:var(--purple);font-weight:500}
.brand-dot{width:14px;height:14px;border-radius:50%;background:var(--purple)}
.socials{display:flex;gap:6px}
.header .socials{left:669px;top:32px}
.soc{width:36px;height:36px;border:1.5px solid #333;border-radius:50%;display:flex;align-items:center;justify-content:center}
.soc span{width:8px;height:8px;border-radius:50%;background:#333}
.call{left:871px;top:30px;width:217px;height:44px;border-radius:22px;background:var(--navy);color:#fff;font-weight:600;font-size:17px;text-align:center;line-height:44px}

.nav{top:133px;left:0;width:1200px;height:38px;background:var(--purple);display:flex;justify-content:center}
.nav a{color:#fff;text-decoration:none;font-size:15px;font-weight:500;line-height:38px;padding:0 17px}
.nav a.active{background:var(--navy)}

.hero{top:171px;left:0;width:1200px;height:399px;background:linear-gradient(100deg,#243321 0%,#4a5a3a 25%,#b46a36 45%,#c97a3e 52%,#6b6a52 65%,#dfe3e8 85%,#f2f3f5 100%)}
.hero-box{left:346px;top:286px;width:509px;height:179px;background:rgba(62,54,105,.72);color:#fff;text-align:center}
.hero-box h1{font-size:46px;margin-top:16px}
.hero-box p{font-size:17px;font-weight:500;line-height:28px;margin-top:14px}

.section-title{width:1200px;left:0;text-align:center;font-size:44px;color:var(--purple)}
.card{width:231px;height:308px;background:var(--card);border:1px solid var(--line)}
.card .ph{height:226px}
.card .name{font-size:17px;margin:20px 0 0 16px;color:#333}
.card .price{font-size:15px;font-weight:600;color:var(--purple);margin:4px 0 0 16px}

.about-img{top:1853px;left:0;width:634px;height:397px;background:linear-gradient(110deg,#3c3a2c 0%,#6c6e4a 30%,#8f9a5c 55%,#5c6a3c 80%,#3a3f2a 100%)}
.about{top:1853px;left:634px;width:566px;height:397px;background:var(--navy);color:#fff;padding:50px 0 0 37px}
.about h2{font-size:42px}
.about p{width:420px;font-size:14.3px;line-height:27.5px;text-align:justify;margin-top:24px}

.touch-bg{top:2250px;left:0;width:1200px;height:500px;background:var(--soft)}
.tbox{top:2437px;width:247px;height:203px;color:#fff;text-align:center;font-size:16px;line-height:24px;padding-top:52px}
.tbox svg{display:block;margin:0 auto 12px}
.tbox.mail{left:223px;background:var(--navy-dark)}
.tbox.phone{left:477px;background:#dcdcdc;color:#444}
.tbox.loc{left:729px;background:#4a3f7a}

.footer{top:2750px;left:0;width:1200px;height:357px;background:var(--purple);color:#fff}
.fcol{top:60px}
.fcol h3{font-size:16px;font-weight:600;letter-spacing:.3px;margin-bottom:22px}
.fcol li{list-style:none;font-size:13px;margin-bottom:10px}
.contact li{display:flex;gap:12px;align-items:flex-start}
.contact svg{flex:none;margin-top:2px}
.contact .u{text-decoration:underline}
.email-field{width:266px;height:38px;border-radius:19px;background:#fff;color:#777;font-size:13px;line-height:38px;padding-left:18px}
.submit{width:155px;height:38px;border-radius:19px;background:var(--navy);font-weight:600;font-size:15px;text-align:center;line-height:38px;margin-top:12px}
.footer .socials{margin:26px 0 0 19px;gap:7px}
.footer .soc{background:#fff;border-color:#fff}
.footer .soc span{background:var(--purple)}
.frule{left:112px;top:290px;width:976px;height:1px;background:rgba(255,255,255,.2)}
.copy{top:312px;left:0;width:1200px;text-align:center;font-size:14px}
</style>
</head>
<body>

<div class="abs topbar">Lorem ipsum dolor sit amet, consectetur adipiscing elit,</div>

<header class="abs header">
  <div class="abs brand"><span class="brand-dot"></span>Bram Kellet Photography</div>
  <div class="abs socials">
    <div class="soc"><span></span></div><div class="soc"><span></span></div>
    <div class="soc"><span></span></div><div class="soc"><span></span></div>
  </div>
  <div class="abs call">Call Us: 555-014-272</div>
</header>

<nav class="abs nav">
  <a>Home</a><a>About Me</a><a class="active">Nature</a><a>Weddings</a><a>Potraits</a><a>Architecture</a><a>Shop</a><a>portfolio</a><a>News</a><a>Contact Us</a>
</nav>

<div class="abs hero" role="img" aria-label="Red fox sitting on snowy rocks among pine branches"></div>
<div class="abs hero-box">
  <h1 class="script">Nature</h1>
  <p>Lorem ipsum dolor sit amet, consectetur adipiscing<br>elit, sed do eiusmod tempor incididunt</p>
</div>

<h2 class="abs section-title script" style="top:645px">Nature Portfolio</h2>

<div class="abs card" style="left:111px;top:748px"><div class="ph" role="img" aria-label="Cascading jungle waterfall" style="background:linear-gradient(160deg,#3f6b3a,#9fb6c8 50%,#3aa3b6)"></div><div class="name">Product Name</div><div class="price">$15.36</div></div>
<div class="abs card" style="left:360px;top:748px"><div class="ph" role="img" aria-label="Kingfisher in flight over water" style="background:radial-gradient(circle at 50% 45%,#c77a3a,#4b6a2a 45%,#2f3f1c)"></div><div class="name">Product Name</div><div class="price">$15.36</div></div>
<div class="abs card" style="left:609px;top:748px"><div class="ph" role="img" aria-label="Two tigers walking on a dirt path" style="background:linear-gradient(180deg,#8a8276,#b59068 50%,#8c7a68)"></div><div class="name">Product Name</div><div class="price">$15.36</div></div>
<div class="abs card" style="left:858px;top:748px"><div class="ph" role="img" aria-label="Pack of wolves on rocks" style="background:linear-gradient(180deg,#7a7c78,#5d5e58 60%,#8e8d86)"></div><div class="name">Product Name</div><div class="price">$15.36</div></div>

<div class="abs card" style="left:111px;top:1091px"><div class="ph" role="img" aria-label="Boat in a turquoise lagoon by limestone cliffs" style="background:linear-gradient(180deg,#2a6fc0,#3f7a3c 45%,#1fa8b8)"></div><div class="name">Product Name</div><div class="price">$15.36</div></div>
<div class="abs card" style="left:360px;top:1091px"><div class="ph" role="img" aria-label="Deer grazing in sunlit meadow under trees" style="background:linear-gradient(170deg,#7a6a2a,#e3d68a 55%,#9aa03e)"></div><div class="name">Product Name</div><div class="price">$15.36</div></div>
<div class="abs card" style="left:609px;top:1091px"><div class="ph" role="img" aria-label="Flower-covered hills under storm clouds" style="background:linear-gradient(180deg,#3c4450,#b8b4a6 40%,#6c9a3c 65%,#c74f9a)"></div><div class="name">Product Name</div><div class="price">$15.36</div></div>
<div class="abs card" style="left:858px;top:1091px"><div class="ph" role="img" aria-label="Puppy and kitten sitting on grass" style="background:linear-gradient(180deg,#141a10,#3a4a1c 50%,#6a8a2a)"></div><div class="name">Product Name</div><div class="price">$15.36</div></div>

<div class="abs card" style="left:111px;top:1434px"><div class="ph" role="img" aria-label="Two bee-eater birds on a branch" style="background:linear-gradient(150deg,#cfe3b0,#5f8a2a 55%,#2f4a1a)"></div><div class="name">Product Name</div><div class="price">$15.36</div></div>
<div class="abs card" style="left:360px;top:1434px"><div class="ph" role="img" aria-label="Autumn trees beside a calm river" style="background:linear-gradient(180deg,#c9902a,#8a4a1a 50%,#6a7a2a)"></div><div class="name">Product Name</div><div class="price">$15.36</div></div>
<div class="abs card" style="left:609px;top:1434px"><div class="ph" role="img" aria-label="Three giraffes on the savanna" style="background:linear-gradient(180deg,#a8b0bc,#c4b8a0 60%,#8c8a6a)"></div><div class="name">Product Name</div><div class="price">$15.36</div></div>
<div class="abs card" style="left:858px;top:1434px"><div class="ph" role="img" aria-label="Lightning over a rocky coastline" style="background:linear-gradient(180deg,#2a4c8c,#8aa0c8 45%,#a8764a 70%,#1f5a7a)"></div><div class="name">Product Name</div><div class="price">$15.36</div></div>

<div class="abs about-img" role="img" aria-label="Photographer shooting with a telephoto lens in a park"></div>
<section class="abs about">
  <h2 class="script">About Me</h2>
  <p>Lorem ipsum dolor sit amet, consectetur adipiscing elit, sed do eiusmod tempor incididunt ut labore et dolore magna aliqua. Ut enim ad minim veniam, quis nostrud exercitation ullamco laboris nisi ut aliquip ex commodo consequat. Duis aute irure dolor reprehenderit voluptate velit esse cillum dolore eu fugiat nulla pariatur. Excepteur sint occaecat cupidatat non proident, sunt in culpa qui officia deserunt mollit anim id est laborum.</p>
</section>

<div class="abs touch-bg"></div>
<h2 class="abs section-title script" style="top:2350px">Get In Touch</h2>
<div class="abs tbox mail">
  <svg width="44" height="44" viewBox="0 0 44 44" fill="none" stroke="#fff" stroke-width="2" stroke-linejoin="round"><path d="M40 4 4 20l14 5 4 15 6-10 12-26z"/><path d="M18 25 40 4"/></svg>
  info@bramkellet<br>photography.example
</div>
<div class="abs tbox phone">
  <svg width="42" height="42" viewBox="0 0 42 42" fill="none" stroke="#444" stroke-width="2" stroke-linecap="round"><path d="M9 5l7 7-4 5c2 5 6 9 11 11l5-4 7 7-5 6C19 36 6 23 4 10z"/><path d="M24 12a8 8 0 0 1 6 6M24 6a14 14 0 0 1 12 12"/></svg>
  555 014 2720<br>555 014 7788
</div>
<div class="abs tbox loc">
  <svg width="34" height="44" viewBox="0 0 34 44" fill="none" stroke="#fff" stroke-width="2"><path d="M17 42S3 26 3 16a14 14 0 0 1 28 0c0 10-14 26-14 26z"/><circle cx="17" cy="16" r="5"/></svg>
  #2868 Lorem ipsum dolor<br>sit amet, consectetur
</div>

<footer class="abs footer">
  <div class="abs fcol contact" style="left:112px">
    <h3>CONTACT INFO</h3>
    <ul>
      <li><svg width="14" height="12" viewBox="0 0 14 12" fill="#fff"><path d="M1 3c0-2 12-2 12 0v2h-3V4H4v1H1z"/><rect x="2" y="6" width="10" height="6" rx="1"/></svg>(555) 014-2720</li>
      <li><svg width="14" height="12" viewBox="0 0 14 12" fill="#fff"><rect x="3" y="0" width="8" height="4"/><rect x="0" y="4" width="14" height="6" rx="1"/><rect x="3" y="8" width="8" height="4"/></svg>(555) 014-272</li>
      <li><svg width="14" height="10" viewBox="0 0 14 10" fill="none" stroke="#fff" stroke-width="1.5"><rect x="1" y="1" width="12" height="8"/><path d="m1 1 6 5 6-5"/></svg><span class="u">hello@kelletstudio.example</span></li>
      <li><svg width="12" height="14" viewBox="0 0 12 14" fill="none" stroke="#fff" stroke-width="1.5"><path d="M6 13S1 8 1 5a5 5 0 0 1 10 0c0 3-5 8-5 8z"/><circle cx="6" cy="5" r="1.6"/></svg><span style="line-height:15px">#2868 Lorem ipsum dolor<br>sit amet, consectetur</span></li>
    </ul>
  </div>
  <div class="abs fcol" style="left:372px">
    <h3>QUICK LINKS</h3>
    <ul><li>Home</li><li>About</li><li>Professional Gamer</li><li>Reviews</li><li>Gallery</li></ul>
  </div>
  <div class="abs fcol" style="left:601px">
    <h3>INFORMATION</h3>
    <ul><li>Terms &amp; Conditions</li><li>Privacy Policy</li><li>Disclaimer</li><li>Site Map</li><li>Contact Us</li></ul>
  </div>
  <div class="abs fcol" style="left:820px">
    <h3>NEWSLETTER SUBSCRIPTION</h3>
    <div class="email-field">Enter your email</div>
    <div class="submit">SUBMIT</div>
    <div class="socials">
      <div class="soc"><span></span></div><div class="soc"><span></span></div>
      <div class="soc"><span></span></div><div class="soc"><span></span></div>
    </div>
  </div>
  <div class="abs frule"></div>
  <div class="abs copy">© Copyright 2020 Bram Kellet Photography, All Rights Reserved</div>
</footer>

</body>
</html>
```